Business Card Design Project : Ridgeline Press

In preparation for market launch, Tamarind's Ridgeline Press require the development of a business card. Ridgeline Press is a Community online publishing web portal. We provide the the city of Whistler located in B.C. (Canada) business directories, News, Classified ads, News, Events and blogs etc.

The main focus of the brand is to help local businesses to corporate with their online advertisement and marketing. Meeting our clients face to face is a must (B2B).

Target Market(s)

The target market is B2B customers. Business Owners to Marketing, advertising Managers

Industry/Entity Type

Business

Requirements
Must have
• - The business card will be two sided.
the BACK side will have our logo which consist of (icon, url,slogan) submited. The logo will be middle and centred.

The FRONT side should have company details:

Company Legal Name: TAMARIND RIDGELINE MEDIA

Owen Farsk
Director of Sales & Marketing

www.tamarindridgeline.biz
owen@tamarindridgeline.biz

Phone: 604 317 8842
#2714 - 582 E. Halvern St.
Vancouver, B.C. V7K2R4 Canada
Nice to have
• - For the "FRONT" side of our business card. You can separate or re-arrange with our logo components (icon, logo,slogan). It does not have to be together.

Also our company legal name is rather long so arrange or organize the name in a way to make it shorter. Your experience and creativity will have to come in play.
Should not have
• should not have other colors beside logo color and black text (2 colors). Also nothing Three dimensional

```html
<!DOCTYPE html>
<html lang="en">
<head>
<meta charset="utf-8">
<title>Ridgeline Press – Business Card</title>
<link rel="stylesheet" href="https://fonts.googleapis.com/css2?family=Roboto:wght@400;700;900&display=swap">
<style>
  :root {
    --brand-blue: #2b7cc4;
    --ink: #111111;
    --paper: #ffffff;
    --stage: #3b3b3b;
    --muted-white: #e8f1fa;
  }
  * { box-sizing: border-box; margin: 0; padding: 0; }
  html, body {
    width: 1200px; height: 900px; overflow: hidden;
    background: var(--stage);
    font-family: "Roboto", Arial, sans-serif;
  }
  .canvas {
    width: 1200px; height: 900px;
    display: flex; flex-direction: column;
    align-items: center; justify-content: center; gap: 50px;
  }
  .card {
    position: relative;
    width: 630px; height: 360px;
    background: var(--paper);
    overflow: hidden;
  }
  .card-shapes { position: absolute; inset: 0; }

  /* Front */
  .company-name {
    position: absolute; left: 30px; top: 26px;
    font-size: 27px; font-weight: 900; color: var(--ink);
    letter-spacing: -0.3px;
  }
  .contact-block {
    position: absolute; left: 30px; top: 112px;
    color: var(--paper);
  }
  .person-name { font-size: 19px; font-weight: 700; letter-spacing: 0.5px; }
  .person-role { font-size: 13px; margin-top: 3px; }
  .contact-list { list-style: none; margin-top: 16px; font-size: 13px; line-height: 1.6; }
  .contact-list li { display: flex; align-items: center; gap: 8px; }
  .contact-list svg { flex: none; }
  .address { margin-top: 6px; font-size: 13px; line-height: 1.45; }

  .front-lockup {
    position: absolute; left: 350px; top: 210px;
  }
  .wordmark-row { display: flex; align-items: center; gap: 10px; }
  .brand-square { width: 16px; height: 16px; background: var(--brand-blue); flex: none; }
  .wordmark { font-size: 21px; font-weight: 900; color: var(--ink); letter-spacing: -0.3px; }
  .slogan { font-size: 17px; color: var(--brand-blue); margin-top: 2px; padding-left: 26px; }

  /* Back */
  .back-lockup {
    position: absolute; left: 0; right: 0; top: 105px;
    display: flex; flex-direction: column; align-items: center;
  }
  .back-lockup .brand-square { width: 34px; height: 34px; margin-bottom: 18px; }
  .back-lockup .wordmark { font-size: 30px; }
  .back-lockup .slogan { font-size: 22px; padding-left: 0; }
  .stripe-black { position: absolute; left: 0; right: 0; top: 286px; height: 14px; background: var(--ink); }
  .stripe-blue { position: absolute; left: 0; right: 0; top: 306px; height: 10px; background: var(--brand-blue); }
  .services {
    position: absolute; left: 0; right: 0; top: 330px;
    text-align: center; font-size: 11px; font-weight: 700;
    letter-spacing: 0.6px; color: var(--ink);
  }
</style>
</head>
<body>
<main class="canvas">

  <section class="card card-front" aria-label="Business card front">
    <svg class="card-shapes" width="630" height="360" viewBox="0 0 630 360" aria-hidden="true">
      <polygon points="0,80 352,80 276,360 0,360" fill="var(--brand-blue)"/>
      <polygon points="362,80 386,80 310,360 286,360" fill="var(--ink)"/>
    </svg>

    <h1 class="company-name">Tamarind Ridgeline Media</h1>

    <div class="contact-block">
      <p class="person-name">OWEN FARSK</p>
      <p class="person-role">Director of Sales &amp; Marketing</p>
      <ul class="contact-list">
        <li>
          <svg width="11" height="14" viewBox="0 0 11 14" aria-hidden="true">
            <rect x="1" y="0.5" width="9" height="13" rx="1.5" fill="none" stroke="#fff" stroke-width="1.3"/>
            <rect x="4" y="11" width="3" height="1" fill="#fff"/>
          </svg>
          <span>604 317 8842</span>
        </li>
        <li>
          <svg width="12" height="12" viewBox="0 0 12 12" aria-hidden="true">
            <rect x="0.5" y="0.5" width="11" height="11" fill="#fff"/>
            <path d="M2 3 L6 7 L10 3" fill="none" stroke="var(--brand-blue)" stroke-width="1.3"/>
          </svg>
          <span>owen@tamarindridgeline.biz</span>
        </li>
      </ul>
      <p class="address">#2714 - 582 E. Halvern St.<br>Vancouver, B.C. V7K2R4 Canada</p>
    </div>

    <div class="front-lockup">
      <div class="wordmark-row">
        <span class="brand-square" aria-hidden="true"></span>
        <span class="wordmark">www.tamarindridgeline.biz</span>
      </div>
      <p class="slogan">Your information gateway</p>
    </div>
  </section>

  <section class="card card-back" aria-label="Business card back">
    <div class="back-lockup">
      <span class="brand-square" aria-hidden="true"></span>
      <span class="wordmark">www.tamarindridgeline.biz</span>
      <p class="slogan">Your information gateway</p>
    </div>
    <div class="stripe-black"></div>
    <div class="stripe-blue"></div>
    <p class="services">BUSINESS DIRECTORY • COMMUNITY NEWS &amp; EVENTS • CLASSIFIEDS • BLOGS</p>
  </section>

</main>
</body>
</html>
```